New Business Card Design Project

Need a design that will create an impact / strong impression towards our clients for our business. We are in the lighting business and we do lighting retrofits for large commercial to industrial clientele.

Target Market(s)

Lighting Industry

Industry/Entity Type

Business

Font styles to use
Other font styles liked:
• we would like to use the font on our logo, not sure what it is though..

Requirements
Must have
• Our logo.
Nice to have
• We are open to suggestions that have to do with lighting.

```html
<!DOCTYPE html>
<html lang="en">
<head>
<meta charset="utf-8">
<title>Lumawell Retrofit Group – Business Cards</title>
<link rel="stylesheet" href="https://fonts.googleapis.com/css2?family=Open+Sans:wght@400;600;700&display=swap">
<style>
  :root {
    --stage: #4a413d;
    --card: #1b1b1c;
    --card-edge: #2a2a2b;
    --silver: #b9b9bb;
    --silver-dim: #8d8d90;
    --green: #2f9a3a;
    --green-light: #43b94c;
    --white: #f2f2f2;
    --rule: #d8d8d8;
  }
  * { box-sizing: border-box; margin: 0; padding: 0; }
  html, body { width: 1200px; height: 864px; overflow: hidden; }
  body {
    background: var(--stage);
    font-family: "Open Sans", Arial, sans-serif;
    position: relative;
  }
  .card {
    position: absolute;
    top: 278px;
    width: 540px;
    height: 309px;
    background: var(--card);
    border: 1px solid var(--card-edge);
    border-radius: 4px;
    box-shadow: 0 14px 30px rgba(0,0,0,.45);
  }
  .card--front { left: 40px; }
  .card--back { left: 620px; }

  /* front */
  .front-brand {
    position: absolute;
    left: 60px; top: 92px;
    display: flex; align-items: center; gap: 12px;
  }
  .brand-name {
    font-weight: 700;
    font-size: 52px;
    letter-spacing: 2px;
    line-height: 1;
  }
  .front-brand .brand-name { color: var(--silver); }
  .brand-square { width: 26px; height: 26px; }
  .front-brand .brand-square { background: var(--silver-dim); }
  .front-tagline {
    position: absolute;
    left: 62px; top: 160px;
    width: 360px;
    border-top: 1px solid var(--silver-dim);
    padding-top: 6px;
    font-size: 11px;
    font-weight: 600;
    letter-spacing: 1.6px;
    text-transform: uppercase;
    color: var(--silver-dim);
  }
  .front-web {
    position: absolute;
    left: 62px; top: 224px;
    font-size: 15px;
    letter-spacing: 1.8px;
    color: var(--silver-dim);
  }

  /* back */
  .back-brand {
    position: absolute;
    right: 30px; top: 40px;
    text-align: right;
  }
  .back-brand .brand-line { display: flex; align-items: center; justify-content: flex-end; gap: 10px; }
  .back-brand .brand-name { color: var(--green); font-size: 40px; }
  .back-brand .brand-square { background: var(--green); width: 20px; height: 20px; }
  .back-brand .brand-legal {
    margin-top: 6px;
    font-size: 9px;
    font-weight: 700;
    letter-spacing: 1.2px;
    text-transform: uppercase;
    color: var(--green);
  }
  .person {
    position: absolute;
    left: 30px; top: 50px;
    color: var(--green);
  }
  .person-name { font-size: 16px; font-weight: 600; text-transform: uppercase; letter-spacing: .5px; }
  .person-title { font-size: 13px; text-transform: uppercase; }
  .contacts {
    position: absolute;
    left: 30px; top: 104px;
    list-style: none;
    color: var(--white);
    font-size: 13.5px;
    line-height: 19px;
  }
  .contacts li { display: flex; align-items: center; gap: 10px; }
  .contacts svg { width: 11px; height: 11px; fill: var(--green); flex: none; }
  .rule {
    position: absolute;
    height: 1px;
    background: var(--rule);
  }
  .rule--main { left: 30px; right: 30px; top: 192px; }
  .address {
    position: absolute;
    right: 30px; bottom: 26px;
    text-align: right;
    color: var(--white);
    font-size: 15px;
    line-height: 20px;
  }
  .address-rule { width: 210px; margin-left: auto; height: 1px; background: var(--rule); margin-bottom: 12px; }
</style>
</head>
<body>

  <section class="card card--front" aria-label="Card front">
    <div class="front-brand">
      <span class="brand-name">LUMAWELL</span>
      <span class="brand-square"></span>
    </div>
    <p class="front-tagline">Lumawell Retrofit Group, LLC</p>
    <p class="front-web">www.lumawellretrofit.com</p>
  </section>

  <section class="card card--back" aria-label="Card back">
    <div class="person">
      <p class="person-name">Daniel Hartley</p>
      <p class="person-title">CEO/Founder</p>
    </div>

    <ul class="contacts">
      <li><svg viewBox="0 0 12 12" aria-hidden="true"><path d="M3 1h2l1 3-1.5 1a7 7 0 0 0 2.5 2.5L8 6l3 1v2a2 2 0 0 1-2 2A8 8 0 0 1 1 3a2 2 0 0 1 2-2z"/></svg>555 201 4837</li>
      <li><svg viewBox="0 0 12 12" aria-hidden="true"><rect x="3" y="0.5" width="6" height="11" rx="1"/></svg>555 318 7206</li>
      <li><svg viewBox="0 0 12 12" aria-hidden="true"><rect x="1" y="4" width="10" height="6" rx="1"/><rect x="3" y="1" width="6" height="3"/></svg>555 642 9915</li>
      <li><svg viewBox="0 0 12 12" aria-hidden="true"><path d="M1 3h10v7H1z"/></svg>daniel@lumawell.com</li>
    </ul>

    <div class="back-brand">
      <div class="brand-line">
        <span class="brand-name">LUMAWELL</span>
        <span class="brand-square"></span>
      </div>
      <p class="brand-legal">Lumawell Retrofit Group, LLC</p>
    </div>

    <div class="rule rule--main"></div>

    <div class="address">
      <div class="address-rule"></div>
      <p>1240 Birchwood Road</p>
      <p>Fairbanks, Alaska 99701</p>
      <p>www.lumawell.com</p>
    </div>
  </section>

</body>
</html>
```